Clear Harbor Business card

We are a company that owns 2 compliance software programs for TV, Radio and Cable industries as well as an online job board. We need a professional business card that incorproates all three logos.

```html
<!DOCTYPE html>
<html lang="en">
<head>
<meta charset="utf-8">
<title>Clear Harbor Business Card</title>
<link href="https://fonts.googleapis.com/css2?family=Montserrat:wght@700&family=Roboto:wght@400;500;700&display=swap" rel="stylesheet">
<style>
  :root {
    --navy: #141456;
    --red: #e8321e;
    --white: #f7f7f5;
    --ink: #2a2a3a;
    --backdrop: #1c1c1e;
    --rule: #b9b9c4;
  }
  * { margin: 0; padding: 0; box-sizing: border-box; }
  html, body { width: 1200px; height: 874px; overflow: hidden; background: var(--backdrop); }
  .stage {
    width: 1200px; height: 874px;
    display: flex; flex-direction: column; align-items: center; justify-content: center; gap: 40px;
  }
  .card { width: 640px; height: 366px; position: relative; overflow: hidden; }
  .card-back { background: var(--navy); color: var(--white); }
  .card-front { background: var(--white); color: var(--ink); }

  .brand-row { display: flex; align-items: center; }
  .brand {
    font-family: "Roboto", sans-serif; font-weight: 700; line-height: 1;
    display: flex; flex-direction: column;
  }
  .brand .brand-name { display: flex; align-items: center; gap: 6px; }
  .brand .brand-dot { width: 10px; height: 10px; border-radius: 50%; background: currentColor; flex: none; }
  .brand .brand-tag { font-weight: 400; font-size: 6px; letter-spacing: 0.5px; margin-top: 4px; text-transform: uppercase; }
  .brand-divider { width: 1.5px; align-self: stretch; background: currentColor; }

  .card-back .brand-row { position: absolute; left: 0; right: 0; top: 130px; justify-content: center; gap: 18px; height: 62px; }
  .card-back .brand { font-size: 22px; }
  .card-back .website {
    position: absolute; left: 0; right: 0; top: 268px; text-align: center;
    font-family: "Roboto", sans-serif; font-size: 15px; letter-spacing: 7px;
  }

  .card-front .brand-row { position: absolute; left: 28px; top: 120px; gap: 10px; height: 46px; color: var(--navy); }
  .card-front .brand { font-size: 15px; }
  .card-front .brand .brand-tag { font-size: 5px; color: var(--ink); }
  .card-front .split { position: absolute; left: 360px; top: 40px; width: 1.5px; height: 230px; background: var(--rule); }

  .contact { position: absolute; left: 390px; top: 44px; }
  .contact .person { font-family: "Montserrat", sans-serif; font-size: 25px; color: var(--navy); letter-spacing: 0.5px; }
  .contact .role { font-family: "Roboto", sans-serif; font-weight: 500; font-size: 17px; color: var(--red); margin-top: 1px; }
  .contact .address { font-family: "Roboto", sans-serif; font-size: 15px; line-height: 1.35; margin-top: 14px; }
  .contact .lines { list-style: none; margin-top: 10px; font-family: "Roboto", sans-serif; font-size: 15px; line-height: 1.45; }
  .contact .lines li { display: flex; align-items: center; gap: 9px; }
  .contact .lines svg { width: 13px; height: 13px; fill: var(--navy); flex: none; }

  .band-red { position: absolute; left: 0; right: 0; bottom: 42px; height: 3px; background: var(--red); }
  .band-navy { position: absolute; left: 0; right: 0; bottom: 0; height: 39px; background: var(--navy); }
</style>
</head>
<body>
<main class="stage">

  <section class="card card-back" aria-label="Card back">
    <div class="brand-row">
      <div class="brand"><span class="brand-name">Clear Harbor</span><span class="brand-tag">Broadcast Compliance</span></div>
      <span class="brand-divider"></span>
      <div class="brand"><span class="brand-name">Tidewire</span><span class="brand-tag">MVPD Compliance</span></div>
      <span class="brand-divider"></span>
      <div class="brand"><span class="brand-name"><span class="brand-dot"></span>StageCall Jobs</span></div>
    </div>
    <p class="website">www.clearharbor.example</p>
  </section>

  <section class="card card-front" aria-label="Card front">
    <div class="brand-row">
      <div class="brand"><span class="brand-name">Clear Harbor</span><span class="brand-tag">Broadcast Compliance</span></div>
      <span class="brand-divider"></span>
      <div class="brand"><span class="brand-name">Tidewire</span><span class="brand-tag">MVPD Compliance</span></div>
      <span class="brand-divider"></span>
      <div class="brand"><span class="brand-name"><span class="brand-dot"></span>StageCall Jobs</span></div>
    </div>
    <span class="split"></span>
    <div class="contact">
      <h1 class="person">EVAN HALE</h1>
      <p class="role">CEO/FOUNDER</p>
      <p class="address">142 Cedar Row<br>Juneau, Alaska 99801</p>
      <ul class="lines">
        <li><svg viewBox="0 0 16 16"><path d="M3 1l3 3-1.5 2c1 2 3 4 5 5L11.5 9.5l3 3-2 2.5C6 14 2 10 1 3z"/></svg>555 210 4418</li>
        <li><svg viewBox="0 0 16 16"><path d="M4 0h8a1 1 0 0 1 1 1v14a1 1 0 0 1-1 1H4a1 1 0 0 1-1-1V1a1 1 0 0 1 1-1zm1 2v10h6V2zm3 11a1 1 0 1 0 0 2 1 1 0 0 0 0-2z"/></svg>555 730 1926</li>
        <li><svg viewBox="0 0 16 16"><path d="M4 1h8v4H4zM1 6h14v6h-3v3H4v-3H1zm4 4v4h6v-4z"/></svg>555 482 6057</li>
        <li><svg viewBox="0 0 16 16"><path d="M0 3h16v10H0zm1.5 1.2V5l6.5 4 6.5-4v-.8L8 8z"/></svg>evan@clearharbor.example</li>
        <li><svg viewBox="0 0 16 16"><circle cx="8" cy="8" r="7"/></svg>www.clearharbor.example</li>
      </ul>
    </div>
    <span class="band-red"></span>
    <span class="band-navy"></span>
  </section>

</main>
</body>
</html>
```